Corvel Capital LLC

Need Professional Business cards for New Investment Fund

Target Market(s)

High Quality investors

Industry/Entity Type

Financial

Contact Information for Business Card

Phone Number +1 555 284 6190
Name Lukas Varenko
Title Fund Manager
email lv@FundCorvel.com
Website www.FundCorvel.com

Colors

Designer to choose colors to be used in the design.

Requirements
Must have
• Must have our Logo and all of the above. Must be made so lettering and loge can be raised

```html
<!DOCTYPE html>
<html lang="en">
<head>
<meta charset="utf-8">
<title>Fund Manager Business Card</title>
<link href="https://fonts.googleapis.com/css2?family=Lato:wght@400;700;900&display=swap" rel="stylesheet">
<style>
  :root {
    --bg: #2a2a2c;
    --card-dark: #1c1d1f;
    --card-pattern: #232427;
    --accent: #22e80a;
    --ink: #101010;
  }
  html, body {
    margin: 0;
    padding: 0;
    width: 1200px;
    height: 1108px;
    overflow: hidden;
    background: var(--bg);
    font-family: "Lato", sans-serif;
  }
  .canvas {
    position: relative;
    width: 1200px;
    height: 1108px;
  }
  .card {
    position: absolute;
    top: 214px;
    width: 420px;
    height: 680px;
    border-radius: 28px;
    overflow: hidden;
    background: var(--card-dark);
  }
  .card-front { left: 150px; }
  .card-back { left: 630px; }
  .card-shapes {
    position: absolute;
    inset: 0;
  }
  .front-wordmark {
    position: absolute;
    top: 150px;
    left: 0;
    width: 420px;
    text-align: center;
    font-weight: 900;
    font-size: 50px;
    letter-spacing: 1px;
    color: var(--accent);
  }
  .contact-block {
    position: absolute;
    top: 505px;
    left: 40px;
    width: 240px;
    text-align: center;
    color: var(--ink);
  }
  .holder-name {
    font-weight: 900;
    font-size: 23px;
    letter-spacing: 0.5px;
    text-transform: uppercase;
    line-height: 1;
  }
  .holder-title {
    font-size: 17px;
    margin-top: 3px;
  }
  .icon-row {
    display: flex;
    align-items: center;
    gap: 6px;
    margin-top: 8px;
  }
  .icon-row .rule {
    flex: 1;
    height: 1px;
    background: var(--ink);
  }
  .icon-row svg { width: 20px; height: 20px; }
  .contact-line {
    font-size: 18px;
    line-height: 22px;
  }
  .contact-line:first-of-type { margin-top: 6px; }
  .back-pattern {
    position: absolute;
    inset: 0;
    background: linear-gradient(160deg, var(--card-pattern), var(--card-dark));
  }
  .back-wordmark {
    position: absolute;
    top: 470px;
    left: 236px;
    font-weight: 900;
    font-size: 28px;
    color: var(--accent);
  }
</style>
</head>
<body>
<main class="canvas">

  <section class="card card-front">
    <svg class="card-shapes" viewBox="0 0 420 680" aria-hidden="true">
      <polygon points="0,232 420,600 420,680 0,680" fill="var(--accent)"/>
      <line x1="0" y1="212" x2="372" y2="538" stroke="var(--accent)" stroke-width="3"/>
      <polygon points="388,546 420,546 420,574" fill="var(--accent)"/>
    </svg>
    <div class="front-wordmark">Velmarr</div>

    <div class="contact-block">
      <div class="holder-name">Lukas Varenko</div>
      <div class="holder-title">Fund Manager</div>
      <div class="icon-row">
        <span class="rule"></span>
        <svg viewBox="0 0 20 20" aria-label="phone" role="img">
          <circle cx="10" cy="10" r="9" fill="none" stroke="var(--ink)" stroke-width="1.5"/>
          <path d="M6.5 6 l2 -0.5 l1 2.2 l-1.2 1 a6 6 0 0 0 2.8 2.8 l1 -1.2 l2.2 1 l-0.5 2 a7 7 0 0 1 -7.3 -7.3z" fill="var(--ink)"/>
        </svg>
        <svg viewBox="0 0 20 20" aria-label="email" role="img">
          <circle cx="10" cy="10" r="9" fill="none" stroke="var(--ink)" stroke-width="1.5"/>
          <rect x="5" y="6.5" width="10" height="7" fill="var(--ink)"/>
          <path d="M5 6.5 L10 10.5 L15 6.5" fill="none" stroke="var(--accent)" stroke-width="1"/>
        </svg>
        <svg viewBox="0 0 20 20" aria-label="website" role="img">
          <circle cx="10" cy="10" r="9" fill="none" stroke="var(--ink)" stroke-width="1.5"/>
          <circle cx="10" cy="10" r="5" fill="none" stroke="var(--ink)" stroke-width="1.2"/>
          <ellipse cx="10" cy="10" rx="2" ry="5" fill="none" stroke="var(--ink)" stroke-width="1"/>
          <line x1="5" y1="10" x2="15" y2="10" stroke="var(--ink)" stroke-width="1"/>
        </svg>
        <span class="rule"></span>
      </div>
      <div class="contact-line">+1 555 284 6190</div>
      <div class="contact-line">lv@FundCorvel.com</div>
      <div class="contact-line">www.FundCorvel.com</div>
    </div>
  </section>

  <section class="card card-back">
    <div class="back-pattern" role="img" aria-label="Faint repeating brand pattern across the card back"></div>
    <div class="back-wordmark">Velmarr</div>
  </section>

</main>
</body>
</html>
```